Acupuncture business needs business card design

I need a business card for an acupuncture clinic called "Harbourlight Wellness"
It will need the following details:
My name: Marcus Pelling
Acupuncturist
Member TVBH
KWF Treatment Provider
Ph numbers: 581 2734 027 418 5620
Email: marcus@hbwel.example.nz
On the back it will need a table with 2 columns for appointments, one column for time and one for date.

Industry/Entity Type

Clinic

Contact Information for Business Card

Marcus Pelling
Acupuncturist
Member TVBH
KWF Treatment Provider
Email: marcus@hbwel.example.nz

Requirements
Must have
• Marcus Pelling
• Acupuncturist
• Member TVBH
• KWF Treatment Provider
• Ph numbers: 581 2734 027 418 5620
• Email: marcus@hbwel.example.nz
• On the back it will need a table with 2 columns for appointments, one column for time and one for date.

```html
<!DOCTYPE html>
<html lang="en">
<head>
<meta charset="utf-8">
<title>Harbourlight Wellness – Business Card</title>
<link rel="stylesheet" href="https://fonts.googleapis.com/css2?family=Open+Sans:wght@400;600;700&display=swap">
<style>
  :root {
    --teal: #137c93;
    --teal-deep: #0f6e84;
    --cyan: #20aee0;
    --white: #ffffff;
    --pale: #cfe3e8;
    --backdrop: #e9ecee;
    --ink-soft: #6f8f98;
  }
  html, body {
    margin: 0;
    width: 1200px;
    height: 948px;
    overflow: hidden;
    background: var(--backdrop);
    font-family: "Open Sans", Arial, sans-serif;
  }
  .sheet {
    position: relative;
    width: 1200px;
    height: 948px;
    display: flex;
    align-items: center;
    justify-content: center;
    gap: 40px;
  }
  .card {
    position: relative;
    width: 540px;
    height: 314px;
    overflow: hidden;
    box-shadow: 0 6px 18px rgba(0,0,0,0.18);
  }

  /* Front */
  .card-front { background: var(--white); }
  .front-shape { position: absolute; inset: 0; }
  .brand {
    position: absolute;
    top: 30px;
    left: 30px;
    display: flex;
    align-items: center;
    gap: 8px;
  }
  .brand-dot {
    width: 20px;
    height: 20px;
    border-radius: 50%;
    background: var(--teal);
  }
  .brand-name {
    font-size: 22px;
    font-weight: 600;
    color: var(--teal);
    letter-spacing: -0.2px;
  }
  .brand-tagline {
    position: absolute;
    top: 62px;
    left: 58px;
    font-size: 7px;
    letter-spacing: 2.4px;
    color: var(--ink-soft);
    text-transform: uppercase;
  }
  .contact {
    position: absolute;
    right: 30px;
    bottom: 26px;
    text-align: right;
    color: var(--white);
  }
  .contact-name {
    font-size: 17px;
    font-weight: 700;
    margin-bottom: 3px;
  }
  .contact-role {
    font-size: 11.5px;
    line-height: 1.45;
  }
  .contact-line {
    display: flex;
    justify-content: flex-end;
    align-items: center;
    gap: 7px;
    font-size: 12px;
    margin-top: 7px;
  }
  .contact-line svg { width: 13px; height: 13px; fill: var(--white); }

  /* Back */
  .card-back { background: var(--teal); color: var(--white); }
  .appointments {
    position: absolute;
    top: 34px;
    left: 44px;
    border-collapse: separate;
    border-spacing: 14px 10px;
  }
  .appointments th {
    font-size: 15px;
    font-weight: 400;
    text-align: left;
    padding-left: 2px;
  }
  .appointments td {
    width: 170px;
    height: 24px;
    background: var(--pale);
    opacity: 0.9;
  }
  .website {
    position: absolute;
    left: 58px;
    bottom: 34px;
    font-size: 17px;
    letter-spacing: 4px;
  }
</style>
</head>
<body>
<main class="sheet">

  <section class="card card-front" aria-label="Card front">
    <svg class="front-shape" viewBox="0 0 540 314" aria-hidden="true">
      <path d="M0,300 C120,170 320,98 540,96" fill="none" stroke="var(--cyan)" stroke-width="6"/>
      <path d="M0,314 L0,312 C120,186 320,114 540,112 L540,314 Z" fill="var(--teal)"/>
    </svg>

    <div class="brand">
      <span class="brand-dot"></span>
      <span class="brand-name">Harbourlight Wellness</span>
    </div>
    <div class="brand-tagline">Acupuncture Physiotherapy</div>

    <div class="contact">
      <div class="contact-name">Marcus Pelling</div>
      <div class="contact-role">Acupuncturist Member TVBH</div>
      <div class="contact-role">KWF Treatment Provider</div>
      <div class="contact-line">
        <svg viewBox="0 0 24 24" aria-hidden="true"><path d="M6.6 10.8a15.1 15.1 0 0 0 6.6 6.6l2.2-2.2c.3-.3.7-.4 1-.2 1.1.4 2.3.6 3.6.6.6 0 1 .4 1 1V20c0 .6-.4 1-1 1A17 17 0 0 1 3 4c0-.6.4-1 1-1h3.5c.6 0 1 .4 1 1 0 1.3.2 2.5.6 3.6.1.3 0 .7-.2 1z"/></svg>
        <span>581 2734 · 027 418 5620</span>
      </div>
      <div class="contact-line">
        <svg viewBox="0 0 24 24" aria-hidden="true"><path d="M2 5h20v14H2z M4 7v.4l8 5.2 8-5.2V7z" fill-rule="evenodd"/></svg>
        <span>marcus@hbwel.example.nz</span>
      </div>
    </div>
  </section>

  <section class="card card-back" aria-label="Card back">
    <table class="appointments">
      <thead>
        <tr><th>Date</th><th>Time</th></tr>
      </thead>
      <tbody>
        <tr><td></td><td></td></tr>
        <tr><td></td><td></td></tr>
        <tr><td></td><td></td></tr>
        <tr><td></td><td></td></tr>
      </tbody>
    </table>
    <div class="website">www.hbwel.example.nz</div>
  </section>

</main>
</body>
</html>
```